Bespoke Builders Business Card Design

We need a business card for an established builder of high quality bespoke homes in Auckland and Northland. We build and renovate homes collaboratively facilitating effective communication between owners, builders, architects, suppliers and tradespeople. We have never built or renovated a home that leaks or has faults. We only use reliable materials. We have never been sued or had legal action taken against us. We are honest builders of bespoke homes not group mass produced homes. Our niche market is in character homes. We practice sustainability and have built a lot of coastal property. We have been in business for over thirty years . We would like to see natural colors of the environment sand,sea and maybe vegetation . The design should communicate quality, sustainability,fair pricing, open communication and the originality of bespoke building. And the fact that the builder is registered.

Industry/Entity Type

Business

Contact Information for Business Card

Rowan Tellick Builders
Ph. 021583917
18 Kestrel Rd Harwood Bay Auckland 0814
PO Box 927 Mangawhai 0583

```html
<!DOCTYPE html>
<html lang="en">
<head>
<meta charset="utf-8">
<title>Rowan Tellick Builders – Business Card</title>
<link rel="stylesheet" href="https://fonts.googleapis.com/css2?family=Old+Standard+TT:wght@700&family=Arimo:wght@400&display=swap">
<style>
  :root {
    --page-bg: #d8d3cb;
    --card-black: #050505;
    --card-white: #f4f4f2;
    --bevel-dark: #3c3c3a;
    --bevel-light: #8a8a86;
    --ink-dark: #111111;
    --ink-light: #ffffff;
  }
  html, body {
    margin: 0;
    width: 1200px;
    height: 892px;
    overflow: hidden;
    background: var(--page-bg);
  }
  .business-card {
    position: absolute;
    left: 75px;
    top: 146px;
    width: 1050px;
    height: 600px;
    box-shadow: 0 10px 30px rgba(0,0,0,0.25);
    overflow: hidden;
  }
  .card-shapes {
    position: absolute;
    inset: 0;
  }
  .company-name {
    position: absolute;
    top: 120px;
    left: 0;
    width: 100%;
    margin: 0;
    text-align: center;
    font-family: "Old Standard TT", "Century Schoolbook", serif;
    font-weight: 700;
    font-size: 74px;
    color: var(--ink-dark);
    letter-spacing: 0.5px;
  }
  .contact-details {
    position: absolute;
    top: 425px;
    left: 0;
    width: 100%;
    margin: 0;
    text-align: center;
    font-family: "Arimo", Arial, sans-serif;
    font-size: 31px;
    line-height: 41px;
    color: var(--ink-light);
  }
  .contact-details .phone { letter-spacing: 1.5px; }
</style>
</head>
<body>
  <div class="business-card">
    <svg class="card-shapes" width="1050" height="600" viewBox="0 0 1050 600" aria-hidden="true">
      <defs>
        <linearGradient id="bevel-shade" x1="0" y1="0" x2="0" y2="1">
          <stop offset="0" stop-color="var(--bevel-light)"/>
          <stop offset="1" stop-color="var(--bevel-dark)"/>
        </linearGradient>
      </defs>
      <rect class="lower-panel" width="1050" height="600" fill="var(--card-black)"/>
      <polygon class="edge-line" points="0,0 1050,0 1050,334 930,404 120,404 0,334" fill="var(--card-white)"/>
      <polygon class="bevel-strip" points="0,0 1050,0 1050,326 930,396 120,396 0,326" fill="url(#bevel-shade)"/>
      <polygon class="upper-panel" points="0,0 1050,0 1050,298 930,368 120,368 0,298" fill="var(--card-white)"/>
    </svg>
    <h1 class="company-name">Rowan Tellick Builders</h1>
    <p class="contact-details">
      <span class="phone">021583917</span><br>
      <span class="street-address">18 Kestrel Rd Harwood Bay Auckland 0814</span><br>
      <span class="postal-address">PO Box 927 Mangawhai 0583</span>
    </p>
  </div>
</body>
</html>
```